Flyer informing about the activities of people in action

Leute im Wandel (www.leuteimwandel.ch) offers coaching, medation, support for traumatized people and conflict and crisis intervention. The flyer should inform about the activities in a plain and simple way (see logo on the homepage).

Target Market(s)

Adults who live in Switzerland or Germany

Requirements
Must have
• - simple flyer, the design is based on my logo. Brief information about my offer, reference to my homepage www.leuteimwandel.
- 2-sided: on the first page - fire circle with text (see homepage - Home), on the back - offer with logo
- possibly a square flyer

Should not have
• no photos

```html
<!DOCTYPE html>
<html lang="de">
<head>
<meta charset="utf-8">
<title>Leute im Wandel – Flyer</title>
<link rel="stylesheet" href="https://fonts.googleapis.com/css2?family=Parisienne&family=Marcellus+SC&family=Raleway:wght@600;700&display=swap">
<style>
  :root {
    --page: #ffffff;
    --ink: #2f2c29;
    --gold: #9a7a2e;
    --gold-text: #a98a4c;
    --swirl: #fde4a6;
    --white: #ffffff;
    --bullet: #d8b45a;
  }
  * { margin: 0; padding: 0; box-sizing: border-box; }
  html, body { width: 1200px; height: 960px; overflow: hidden; background: var(--page); }
  .canvas { position: relative; width: 1200px; height: 960px; }

  .card { position: absolute; top: 232px; width: 495px; height: 495px; overflow: hidden; }
  .card--front { left: 79px; background: var(--page); box-shadow: 0 0 0 1px #ececec; }
  .card--back { left: 626px; background: var(--gold); color: var(--white); }

  .script { font-family: "Parisienne", cursive; font-weight: 400; }
  .caps { font-family: "Marcellus SC", serif; letter-spacing: 0.08em; }
  .url { font-family: "Raleway", sans-serif; font-weight: 700; font-size: 15px; white-space: nowrap; }

  /* front */
  .fire-circle { position: absolute; left: 35px; top: 48px; width: 414px; height: 426px; }
  .front__headline { position: absolute; left: 43px; top: 102px; font-size: 30px; color: var(--ink); white-space: nowrap; }
  .front__lead { position: absolute; left: 43px; top: 150px; font-size: 17px; line-height: 29px; letter-spacing: 0.13em; color: var(--ink); text-transform: uppercase; white-space: nowrap; }
  .front__focus { position: absolute; right: 50px; top: 259px; text-align: right; color: var(--ink); }
  .front__focus-title { font-size: 17px; letter-spacing: 0.1em; text-transform: uppercase; margin-bottom: 8px; white-space: nowrap; }
  .front__focus-text { font-size: 15px; line-height: 22px; letter-spacing: 0.1em; text-align: center; white-space: nowrap; }
  .brand { position: absolute; display: flex; align-items: center; gap: 7px; font-family: "Marcellus SC", serif; font-size: 15px; white-space: nowrap; }
  .brand__dot { flex: none; width: 26px; height: 26px; border-radius: 50%; border: 3px solid currentColor; }
  .front__brand { left: 96px; top: 428px; color: var(--gold-text); }
  .front__url { position: absolute; left: 262px; top: 440px; font-size: 16px; color: var(--gold-text); }

  /* back */
  .back__brand { left: 46px; top: 36px; color: var(--white); }
  .back__url { position: absolute; right: 46px; top: 39px; color: var(--white); font-size: 15px; }
  .back__headline { position: absolute; left: 0; right: 0; top: 120px; text-align: center; font-size: 30px; white-space: nowrap; }
  .back__sub { position: absolute; left: 0; right: 0; top: 172px; text-align: center; font-size: 12px; letter-spacing: 0.2em; text-transform: uppercase; white-space: nowrap; }
  .offers { position: absolute; left: 22px; right: 26px; top: 214px; list-style: none; }
  .offer { position: relative; padding-left: 28px; margin-bottom: 16px; }
  .offer::before { content: ""; position: absolute; left: 0; top: 3px; width: 17px; height: 17px; border-radius: 50%; border: 3px solid var(--bullet); }
  .offer__title { font-family: "Marcellus SC", serif; font-weight: 400; font-size: 15px; letter-spacing: 0.07em; line-height: 20px; text-transform: uppercase; white-space: nowrap; }
  .offer__text { font-family: "Marcellus SC", serif; font-size: 11px; line-height: 16px; letter-spacing: 0.09em; text-transform: uppercase; }
</style>
</head>
<body>
<div class="canvas">

  <section class="card card--front">
    <svg class="fire-circle" viewBox="0 0 414 426" role="img" aria-label="Hand-drawn golden fire circle">
      <ellipse cx="200" cy="215" rx="195" ry="205" fill="var(--swirl)" opacity="0.75"/>
    </svg>
    <h1 class="front__headline script">Sie möchten ... weiterkommen</h1>
    <p class="front__lead caps">Ihre belastende Situation lösen.<br>Ihre wichtigen Fragen klären.</p>
    <div class="front__focus caps">
      <p class="front__focus-title">Leichter weiterkommen</p>
      <p class="front__focus-text">in der frustrierenden Zusammenarbeit<br>oder Ihrem mühsamen (Zusammen-)Leben.</p>
    </div>
    <div class="brand front__brand"><span class="brand__dot"></span>Leute im Wandel</div>
    <p class="front__url url">www.leuteimwandel.ch</p>
  </section>

  <section class="card card--back">
    <div class="brand back__brand"><span class="brand__dot"></span>Leute im Wandel</div>
    <p class="back__url url">www.leuteimwandel.ch</p>
    <h2 class="back__headline script">Ich begleite Sie und bringe Ihnen</h2>
    <p class="back__sub caps">Orientierung, Klarheit &amp; Unterstützung</p>
    <ul class="offers">
      <li class="offer">
        <h3 class="offer__title">Coaching</h3>
        <p class="offer__text">Manchmal braucht man ein Gegenüber zum Klären der eigenen Situation oder beim Entdecken neuer Sichtweisen und Handlungsmöglichkeiten.</p>
      </li>
      <li class="offer">
        <h3 class="offer__title">Mediation</h3>
        <p class="offer__text">Gewisse Konflikte können Sie nicht mehr selber lösen. Wenige Worte entzünden einen erbitterten Streit oder erzeugen eisige Stille.</p>
      </li>
      <li class="offer">
        <h3 class="offer__title">Begleitung von traumatisierten Menschen</h3>
        <p class="offer__text">Ihr Leben fühlt sich oft schwer, bedrückend und freudlos an. Erfolglos haben Sie probiert, sich von dieser Kontakt- und Perspektivlosigkeit zu befreien.</p>
      </li>
    </ul>
  </section>

</div>
</body>
</html>
```